Creative, fresh business card design for Ripplecraft Facades

We need a fresh, creative business card design for Ripplecraft Facades. We are the manufacturer of Ripplecraft Facades in Australia. Wall panels are 2400 x 1200mm panels made from MDF and feature 3D patterns on the face of the panel. The colours to be used are green, silver/grey and white RGB
Red 187
Green 207
Blue 65.

An idea is to possibly use a watermark of one of our designs as a background (like on the "Grids" design on the left hand side of page 2 of our brochure).

Target Market(s)

Interior designers, architects, builders and home renovators

Industry/Entity Type

Business

Contact Information for Business Card

Details to go on the card are:
Our logo (attached),
Slogan: "Decorative panels for interiors and exteriors",
Contact name,
Position,
Mobile phone number,
Business address,
Business phone,
Business fax,
Website and
Email address.

I have attached a few images of our panels and our brochure for reference.

The colours of the business card should feature our logo colours which are: RGB
Red 187
Green 207
Blue 65

Requirements
Must have
• Very modern fonts and design. Some of the designs shown especially the "Prisms" design which is a popular design.
Nice to have
• Creative but simple design. Very contemporary.
Should not have
• Anything ornate or old fashioned.

```html
<!DOCTYPE html>
<html lang="en">
<head>
<meta charset="utf-8">
<title>Ripplecraft Facades – Business Card</title>
<link rel="stylesheet" href="https://fonts.googleapis.com/css2?family=Arimo:wght@400;700&display=swap">
<style>
  :root {
    --brand-green: rgb(187, 207, 65);
    --brand-grey: #8a8b8d;
    --text-dark: #4a4a4a;
    --card-white: #ffffff;
    --backdrop: #ecece8;
  }
  html, body {
    margin: 0;
    padding: 0;
    width: 1200px;
    height: 987px;
    overflow: hidden;
    background: var(--backdrop);
    font-family: "Arimo", Arial, sans-serif;
  }
  .canvas {
    position: relative;
    width: 1200px;
    height: 987px;
  }
  .card {
    position: absolute;
    width: 615px;
    height: 350px;
    box-shadow: 0 2px 8px rgba(0,0,0,0.12);
  }
  .card--front { left: 293px; top: 131px; background: var(--card-white); }
  .card--back  { left: 292px; top: 506px; background: var(--brand-green); }

  .accent-bar {
    position: absolute;
    left: 0; top: 89px;
    width: 12px; height: 40px;
    background: var(--brand-green);
  }
  .person { position: absolute; left: 42px; top: 88px; }
  .person__name {
    margin: 0;
    font-size: 23px; font-weight: 700;
    color: var(--brand-green);
    letter-spacing: 0.3px;
  }
  .person__role {
    margin: 3px 0 0;
    font-size: 17px;
    color: var(--brand-grey);
  }
  .address {
    position: absolute; left: 42px; top: 147px;
    font-size: 17px; line-height: 22px;
    color: var(--text-dark);
    font-style: normal;
  }
  .contact-list {
    position: absolute; left: 42px; top: 200px;
    margin: 0; padding: 0; list-style: none;
    font-size: 17px; color: var(--text-dark);
  }
  .contact-list li {
    display: flex; align-items: center;
    height: 23.5px;
  }
  .contact-list svg {
    width: 15px; height: 15px;
    margin-right: 10px;
    fill: var(--brand-green);
    flex: none;
  }

  .brand { position: absolute; text-align: left; }
  .brand__lockup { display: flex; align-items: center; gap: 12px; }
  .brand__mark {
    width: 46px; height: 46px; flex: none;
  }
  .brand__name {
    font-size: 30px; font-weight: 700; line-height: 32px;
  }
  .brand__tagline {
    margin: 14px 0 0;
    font-size: 12.5px; line-height: 15px;
    letter-spacing: 2.4px;
    text-align: center;
  }
  .card--front .brand { left: 350px; top: 120px; width: 212px; }
  .card--front .brand__mark { background: var(--brand-green); }
  .card--front .brand__name { color: var(--brand-grey); }
  .card--front .brand__tagline { color: var(--brand-grey); }

  .card--back .brand { left: 394px; top: 168px; width: 190px; }
  .card--back .brand__mark { background: var(--card-white); }
  .card--back .brand__name { color: var(--card-white); font-size: 27px; line-height: 30px; }
  .card--back .brand__tagline { color: var(--card-white); font-size: 11.5px; letter-spacing: 2px; }
  .brand__web {
    margin: 6px 0 0;
    font-size: 15px; color: var(--card-white);
    text-align: center;
  }
</style>
</head>
<body>
<main class="canvas">

  <section class="card card--front" aria-label="Business card front">
    <span class="accent-bar"></span>
    <div class="person">
      <h1 class="person__name">DANIEL MARSH</h1>
      <p class="person__role">CEO&amp;Founder</p>
    </div>
    <address class="address">
      412 Kestrel Avenue<br>
      Geelong, Victoria 3220
    </address>
    <ul class="contact-list">
      <li>
        <svg viewBox="0 0 16 16" aria-hidden="true"><path d="M3.6 1.2l2.3 2.6-1.3 1.9c.9 2 2.4 3.6 4.4 4.6l1.9-1.3 2.6 2.3-1.4 2.3C7 13.3 2.6 8.9 1.3 3.1z"/></svg>
        (555) 214-7306
      </li>
      <li>
        <svg viewBox="0 0 16 16" aria-hidden="true"><path d="M4 1h7l1 1v3H4zM1 6h14v6h-3v3H4v-3H1zm4 4v4h6v-4z"/></svg>
        (555) 214-7391
      </li>
      <li>
        <svg viewBox="0 0 16 16" aria-hidden="true"><path d="M1 3h14v1L8 9 1 4zm0 3l7 5 7-5v7H1z"/></svg>
        dmarsh@ripplecraftfacades.com
      </li>
      <li>
        <svg viewBox="0 0 16 16" aria-hidden="true"><circle cx="8" cy="8" r="7"/><path d="M5 4c2 1 1 3 3 3s1 3 0 4M10 2c0 2 2 2 3 4" stroke="#fff" stroke-width="1.2" fill="none"/></svg>
        www.ripplecraftfacades.com
      </li>
    </ul>
    <div class="brand">
      <div class="brand__lockup">
        <span class="brand__mark"></span>
        <span class="brand__name">Ripplecraft<br>Facades</span>
      </div>
      <p class="brand__tagline">decorative panels for<br>interiors &amp; landscapes</p>
    </div>
  </section>

  <section class="card card--back" aria-label="Business card back">
    <div class="brand">
      <div class="brand__lockup">
        <span class="brand__mark"></span>
        <span class="brand__name">Ripplecraft<br>Facades</span>
      </div>
      <p class="brand__tagline">decorative panels for<br>interiors &amp; landscapes</p>
      <p class="brand__web">www.ripplecraftfacades.com</p>
    </div>
  </section>

</main>
</body>
</html>
```